letterhead design using our existing logo

We are a small boutique property management business based in Sydney's Northern Beaches.
We are after a sleek, simple modern letterhead (A4) incorporating our logo and its colours.
Also matching envelope (DL)
I have attached the logo with black text and white text for design options.

Target Market(s)

29-69yo Male and Female

Industry/Entity Type

Property Management

Requirements
Must have
• - Harbourline Estates logo
• - Address, number and website:
• Suite 7, 12-14 Wattlegrove Parade, Manly NSW 2095
• Tel: Carl Dorsey 0491 570 163 Marisol Quade 0491 570 218 www.harbourlinestatesgroup.com.au
Nice to have
• sleek design that looks modern and professional
Should not have
• too many colours or too busy

```html
<!DOCTYPE html>
<html lang="en">
<head>
<meta charset="utf-8">
<title>Harbourline Estates — Stationery</title>
<link href="https://fonts.googleapis.com/css2?family=Open+Sans:wght@400;600;700&display=swap" rel="stylesheet">
<style>
  :root {
    --bg: #ededed;
    --paper: #f4f4f4;
    --ink: #232628;
    --teal: #2f8e93;
    --grey: #6b6e70;
    --white: #f2f2f2;
  }
  * { box-sizing: border-box; margin: 0; padding: 0; }
  html, body { width: 1200px; height: 795px; overflow: hidden; background: var(--bg); }
  body { position: relative; font-family: "Open Sans", Arial, sans-serif; color: var(--ink); }

  .sheet { position: absolute; background: var(--paper); overflow: hidden; }
  .dark { background: var(--ink); }

  .brand { display: flex; align-items: center; gap: 5px; font-weight: 600; letter-spacing: 0.02em; white-space: nowrap; }
  .brand .dot { border-radius: 50%; background: var(--teal); flex: none; }
  .brand--ink { color: var(--ink); }
  .brand--light { color: var(--white); }

  /* Letterhead A4 */
  .letterhead { left: 292px; top: 99px; width: 293px; height: 414px; }
  .letterhead .brand { position: absolute; left: 16px; top: 25px; font-size: 8px; }
  .letterhead .brand .dot { width: 6px; height: 6px; }
  .letterhead .rule { position: absolute; left: 16px; right: 14px; top: 43px; height: 1px; background: var(--ink); }
  .contacts { position: absolute; right: 14px; top: 12px; font-size: 5px; line-height: 6.5px; }
  .contacts .name { color: var(--teal); font-weight: 700; }
  .contacts .tel { color: var(--grey); display: flex; align-items: center; gap: 2px; margin-bottom: 2px; }
  .contacts svg { width: 4px; height: 4px; fill: var(--teal); }
  .letterhead .footer { position: absolute; left: 0; right: 0; bottom: 12px; text-align: center; font-size: 5px; line-height: 7px; color: var(--grey); }
  .footer .sep { color: var(--teal); padding: 0 3px; }

  /* Presentation folder */
  .folder { left: 636px; top: 80px; width: 346px; height: 436px; }
  .folder .brand { position: absolute; left: 50%; top: 200px; transform: translateX(-50%); font-size: 21px; gap: 8px; }
  .folder .brand .dot { width: 14px; height: 14px; }

  /* Business cards */
  .card { left: 187px; width: 132px; height: 75px; }
  .card--front { top: 550px; }
  .card--back { top: 647px; }
  .card--front .brand { position: absolute; left: 7px; top: 34px; font-size: 4.2px; gap: 2px; letter-spacing: 0; }
  .card--front .brand .dot { width: 3px; height: 3px; }
  .card .details { position: absolute; left: 68px; top: 20px; font-size: 3.1px; line-height: 4.6px; color: var(--grey); white-space: nowrap; }
  .card .details .name { color: var(--teal); font-weight: 700; font-size: 4.4px; line-height: 5.5px; margin-bottom: 1px; }
  .card--back .brand { position: absolute; left: 50%; top: 33px; transform: translateX(-50%); font-size: 7px; gap: 3px; }
  .card--back .brand .dot { width: 5px; height: 5px; }

  /* DL envelope front */
  .envelope { top: 562px; width: 329px; height: 156px; }
  .envelope--front { left: 353px; }
  .envelope--front .brand { position: absolute; left: 13px; top: 22px; font-size: 9.5px; }
  .envelope--front .brand .dot { width: 7px; height: 7px; }
  .envelope .return { position: absolute; left: 13px; bottom: 12px; font-size: 5px; line-height: 6.5px; color: var(--grey); }

  /* DL envelope back */
  .envelope--back { left: 713px; }
  .envelope--back svg { position: absolute; left: 0; top: 0; }
</style>
</head>
<body>

  <section class="sheet letterhead" aria-label="Letterhead">
    <div class="brand brand--ink"><span>HARBOURLINE ESTATES</span><span class="dot"></span></div>
    <div class="contacts">
      <div class="name">Carl Dorsey</div>
      <div class="tel"><svg viewBox="0 0 10 10"><path d="M2 0l2 2-1 2c1 1 2 2 3 3l2-1 2 2-2 2C4 10 0 6 0 2z"/></svg>0491 570 163</div>
      <div class="name">Marisol Quade</div>
      <div class="tel"><svg viewBox="0 0 10 10"><path d="M2 0l2 2-1 2c1 1 2 2 3 3l2-1 2 2-2 2C4 10 0 6 0 2z"/></svg>0491 570 218</div>
    </div>
    <div class="rule"></div>
    <div class="footer">
      Suite 7, 12-14 Wattlegrove Parade, Manly NSW 2095<br>
      E : info@harbourlinestatesgroup.com.au<span class="sep">|</span>W : www.harbourlinestatesgroup.com.au
    </div>
  </section>

  <section class="sheet dark folder" aria-label="Presentation folder">
    <div class="brand brand--light"><span>HARBOURLINE ESTATES</span><span class="dot"></span></div>
  </section>

  <section class="sheet card card--front" aria-label="Business card front">
    <div class="brand brand--ink"><span>HARBOURLINE ESTATES</span><span class="dot"></span></div>
    <div class="details">
      <div class="name">Carl Dorsey</div>
      Suite 7<br>12-14 Wattlegrove Parade<br>Manly NSW 2095<br>
      0491 570 163<br>carl@harbourlinestatesgroup.com.au<br>www.harbourlinestatesgroup.com.au
    </div>
  </section>

  <section class="sheet dark card card--back" aria-label="Business card back">
    <div class="brand brand--light"><span>HARBOURLINE ESTATES</span><span class="dot"></span></div>
  </section>

  <section class="sheet envelope envelope--front" aria-label="DL envelope front">
    <div class="brand brand--ink"><span>HARBOURLINE ESTATES</span><span class="dot"></span></div>
    <div class="return">Suite 7<br>12-14 Wattlegrove Parade<br>Manly NSW 2095</div>
  </section>

  <section class="sheet envelope envelope--back" aria-label="DL envelope back">
    <svg width="329" height="156" viewBox="0 0 329 156">
      <path d="M0 0H329L324 62Q323 69 316 69H13Q6 69 5 62Z" fill="var(--ink)"/>
      <circle cx="164.5" cy="28" r="5" fill="var(--teal)"/>
    </svg>
  </section>

</body>
</html>
```